Computer Training in the Education sector - Letterhead

We need a new letter head to be designed for the company. We provide computer training fro the Education Sector, both primary and private tertiary providers. The colours will need to tie in with the website www.crossingthestream.co.nz.
The company name is Crossing the Stream with the tag line of Computer Training for Educators.
The footer will need to have the following detail...
0508 PCS MENTOR
021 839 415
www.crossingthestream.co.nz / training@crossingthestream.co.nz
Updates

Thanks for the designs so far.

Some have watermarks in the background. Please don't worry about using watermarks as I will not be using a watermark in in a final design.
Regards,
Roger

Thank you for all the designs and the effort. There was some great concepts that came through.

Cheers
Roger

Industry/Entity Type

Computer

```html
<!DOCTYPE html>
<html lang="en">
<head>
<meta charset="utf-8">
<title>Crossing the Stream – Letterhead</title>
<link rel="stylesheet" href="https://fonts.googleapis.com/css2?family=Arimo:wght@400;700&display=swap">
<style>
  :root {
    --backdrop: #e9e7e4;
    --paper: #ffffff;
    --header-band: #18191b;
    --header-text: #f2f2f2;
    --divider: #8a8a8a;
    --brand-blue: #3a7fd5;
    --brand-orange: #ee7d2b;
    --tagline: #1c1c1c;
  }
  * { margin: 0; padding: 0; box-sizing: border-box; }
  html, body {
    width: 1034px;
    height: 1200px;
    overflow: hidden;
    background: var(--backdrop);
    font-family: "Arimo", Arial, sans-serif;
  }
  .letterhead {
    position: absolute;
    left: 78px;
    top: 31px;
    width: 878px;
    height: 1138px;
    background: var(--paper);
    box-shadow: 0 2px 10px rgba(0,0,0,0.18);
  }
  .header-band {
    position: absolute;
    left: 0; top: 0;
    width: 100%;
    height: 184px;
    background: var(--header-band);
  }
  .brand {
    position: absolute;
    left: 40px;
    top: 58px;
    display: flex;
    align-items: center;
    gap: 12px;
  }
  .brand-mark {
    width: 54px;
    height: 54px;
    border-radius: 50%;
    background: var(--brand-orange);
    flex: none;
  }
  .brand-name {
    width: 120px;
    color: var(--brand-blue);
    font-size: 23px;
    font-weight: 400;
    line-height: 1.05;
  }
  .contact-divider {
    position: absolute;
    left: 553px;
    top: 56px;
    width: 1px;
    height: 80px;
    background: var(--divider);
  }
  .contact-list {
    position: absolute;
    left: 570px;
    top: 54px;
    list-style: none;
    color: var(--header-text);
    font-size: 15.5px;
    letter-spacing: 0.5px;
  }
  .contact-list li {
    display: flex;
    align-items: center;
    gap: 5px;
    height: 24px;
  }
  .contact-icon {
    width: 13px;
    height: 13px;
    flex: none;
  }
  .tagline {
    position: absolute;
    left: 104px;
    top: 1048px;
    color: var(--tagline);
    font-size: 17px;
    font-weight: 700;
    letter-spacing: 1.6px;
  }
</style>
</head>
<body>
  <main class="letterhead">
    <header class="header-band">
      <div class="brand">
        <span class="brand-mark"></span>
        <span class="brand-name">Crossing the Stream</span>
      </div>

      <span class="contact-divider"></span>

      <ul class="contact-list">
        <li>
          <svg class="contact-icon" viewBox="0 0 16 16" aria-hidden="true">
            <circle cx="8" cy="8" r="7" fill="none" stroke="#f2f2f2" stroke-width="1.3"/>
            <path d="M5.5 4.5 L7 4 L7.8 6.2 L6.8 7 Q7.6 8.8 9 9.2 L9.8 8.3 L12 9 L11.5 10.6 Q7 11.5 5.5 4.5Z" fill="#f2f2f2"/>
          </svg>
          0508 PCS MENTOR
        </li>
        <li>
          <svg class="contact-icon" viewBox="0 0 16 16" aria-hidden="true">
            <circle cx="8" cy="8" r="7" fill="none" stroke="#f2f2f2" stroke-width="1.3"/>
            <path d="M5.5 4.5 L7 4 L7.8 6.2 L6.8 7 Q7.6 8.8 9 9.2 L9.8 8.3 L12 9 L11.5 10.6 Q7 11.5 5.5 4.5Z" fill="#f2f2f2"/>
          </svg>
          021 839 415
        </li>
        <li>
          <svg class="contact-icon" viewBox="0 0 16 16" aria-hidden="true">
            <path d="M2 7 L8 3 L14 7 V13 H2Z" fill="#f2f2f2"/>
            <path d="M2 7 L8 11 L14 7" fill="none" stroke="#18191b" stroke-width="1.2"/>
          </svg>
          training@crossingthestream.co.nz
        </li>
        <li>
          <svg class="contact-icon" viewBox="0 0 16 16" aria-hidden="true">
            <g fill="none" stroke="#f2f2f2" stroke-width="1.1">
              <circle cx="8" cy="8" r="6.5"/>
              <ellipse cx="8" cy="8" rx="3" ry="6.5"/>
              <line x1="1.5" y1="8" x2="14.5" y2="8"/>
              <line x1="2.5" y1="4.8" x2="13.5" y2="4.8"/>
              <line x1="2.5" y1="11.2" x2="13.5" y2="11.2"/>
            </g>
          </svg>
          www.crossingthestream.co.nz
        </li>
      </ul>
    </header>

    <p class="tagline">Computer Training for Educators</p>
  </main>
</body>
</html>
```